Hello Creative Minds!
Our business is after a elegant and classy flyer that draws attention!
The business is Velvet Turf - Lawn Revival Services. We provide services that maintain a healthy and vibrant green lawn through the tough Australian seasons. The products we use limits the water needed to keep grass green to a minimum - practically none at all! This not only helps the home owner or home seller but the environment by limiting the use of water that is needed to create a green lawn. The products we use are made from natural ingredients that are and pet friendly.
This fly will be our introductory offer to the market. Below are the required points that need to be on the flyer. Attached is the business logo, before & after pictures and 1 example of the LAYOUT not DESIGN of what the flyer should be laid out like or similar to. Feel free to use different 'Lawn Mower' pictures.
All the best; if you need any questions answered please feel free to message.
REQUIRED POINTS (Please re-phrase were possible);
*Instantly restores the natural green colour of grass – year round
*Lasts for up to 3 months
*Substantially reduces watering needs
*Pet friendly
*Stays green during droughts and water restrictions
*UV fade resistant
*Won’t bleed, run, or stain once absorbed into the grass
*Safe for the environment, pets and people
*Works in extreme heat, cold and frost
*Organic and natural – no harmful chemicals
*Reduces the amount of fertilizer
and water used on lawns
*Kerb appeal is essential for getting your property sold for the highest price possible
SERVICES & PRICING
Lawn maintenance (cut & trim) starting from $60
Lawn rejuvenation starting from $80 (Only $27 a month for 3 months)*
Package deal starting from $120
Introductory offer: 25% off all services. Refer a friend, when they book you receive another 25% off your next service.
LOCATIONS
Nowra to Sydney
CONTACT NUMBER
Will be posted with the winner - please leave an area for this.
SOCIAL MEDIA
Please add Chatterbook and Snapgrid logo's
Updates
Target Market(s)
home owners, home sellers, property developers, real estates and nursing homes and government housing.
Industry/Entity Type
Lawn Care
Look and feel
Each slider illustrates characteristics of the customer's brand and the style your logo design should communicate.

```html
<!DOCTYPE html>
<html lang="en">
<head>
<meta charset="utf-8">
<title>Velvet Turf - Lawn Revival Services Flyer</title>
<link href="https://fonts.googleapis.com/css2?family=Merriweather:wght@300;400;700;900&display=swap" rel="stylesheet">
<style>
  :root{
    --bg:#d9d9d9;
    --paper:#ffffff;
    --ink:#2b2f38;
    --panel:#2c3039;
    --lime:#8cc63f;
    --lime-dark:#6fa62a;
    --grass-1:#4f9a2e;
    --grass-2:#2f6e1e;
  }
  *{box-sizing:border-box;margin:0;padding:0}
  html,body{width:1200px;height:860px;overflow:hidden;background:var(--bg)}
  body{font-family:"Merriweather",Georgia,serif;color:var(--ink)}
  .flyer{position:absolute;left:300px;top:20px;width:600px;height:820px;background:var(--paper);overflow:hidden;box-shadow:0 6px 24px rgba(0,0,0,.18)}
  .flyer-bg{position:absolute;inset:0}
  .headline{position:absolute;left:34px;top:34px;font-weight:900;font-size:34px;line-height:1.1;color:var(--ink);text-shadow:0 0 6px rgba(255,255,255,.55)}
  .pricing-panel{position:absolute;left:50px;top:240px;width:255px;height:505px;background:var(--panel);border-radius:22px;box-shadow:0 8px 0 var(--lime);color:#fff;text-align:center;padding:116px 16px 0}
  .logo-badge{position:absolute;left:72px;top:140px;width:210px;height:210px;border-radius:50%;background:radial-gradient(circle at 50% 40%,#3a3f49,var(--panel));border:6px solid #fff;display:flex;align-items:center;justify-content:center}
  .logo-badge .brand-name{font-size:28px;font-weight:400;color:#fff}
  .section-title{font-size:15px;font-weight:700;color:var(--lime);padding-bottom:7px;border-bottom:1px solid rgba(255,255,255,.12);margin-bottom:4px}
  .price-item{padding:7px 0;border-bottom:1px solid rgba(255,255,255,.12);font-size:12px;line-height:1.4}
  .price-item strong{display:block;font-size:14px;font-weight:700}
  .price-item .price{display:block;font-size:19px;font-weight:900;color:var(--lime)}
  .price-item .note{display:block;color:var(--lime);font-size:11px}
  .intro-offer{padding-top:9px;font-size:13px;line-height:1.35}
  .intro-offer strong{display:block;font-size:14px;font-weight:700}
  .intro-offer .offer{display:block;color:var(--lime);font-weight:700;font-size:12px}
  .intro-offer small{display:block;font-size:8.5px;font-weight:300;line-height:1.4;margin-top:3px}
  .benefits{position:absolute;left:325px;top:440px;width:265px;list-style:none;font-size:11px;line-height:1.33}
  .benefits li{position:relative;padding-left:20px;margin-bottom:4px}
  .benefits svg{position:absolute;left:0;top:2px;width:13px;height:13px}
  .phone{position:absolute;left:140px;top:770px;display:flex;align-items:center;gap:8px;font-size:22px;font-weight:700;color:var(--ink)}
  .phone svg{width:24px;height:24px}
  .social{position:absolute;right:24px;top:782px;display:flex;align-items:center;gap:10px;font-size:12px;font-weight:700;color:var(--ink)}
  .social .network{display:flex;align-items:center;gap:4px;font-weight:400}
  .social .dot{width:10px;height:10px;border-radius:50%;background:var(--ink)}
</style>
</head>
<body>
<main class="flyer">
  <svg class="flyer-bg" viewBox="0 0 600 820" width="600" height="820">
    <defs>
      <linearGradient id="grass" x1="0" y1="0" x2="0" y2="1">
        <stop offset="0" stop-color="#1f4a14"/>
        <stop offset=".2" stop-color="#4f9a2e"/>
        <stop offset="1" stop-color="#5ea83a"/>
      </linearGradient>
    </defs>
    <rect role="img" aria-label="Photo of a lawn mower cutting a lush green lawn" x="0" y="0" width="600" height="470" fill="url(#grass)"/>
    <path class="accent-curve" d="M230,440 C390,420 520,320 600,110 L600,210 C520,360 400,430 230,440 Z" fill="#8cc63f"/>
    <path class="paper-sweep" d="M0,450 C220,450 420,380 520,220 C560,150 585,90 600,40 L600,150 C520,330 400,420 230,440 C140,450 60,450 0,452 Z" fill="#ffffff"/>
    <path d="M0,452 C60,450 140,450 230,440 C400,430 520,360 600,210 L600,820 L0,820 Z" fill="#ffffff"/>
    <path class="footer-wave" d="M0,820 L0,800 C160,812 320,795 460,772 C520,762 570,752 600,745 L600,820 Z" fill="#8cc63f"/>
    <path d="M0,820 C200,817 380,800 600,770 L600,820 Z" fill="#6fa62a" opacity=".55"/>
  </svg>

  <h1 class="headline">Lawn<br>Revival Services</h1>

  <section class="pricing-panel">
    <h2 class="section-title">SERVICES &amp; PRICING</h2>
    <div class="price-item">
      <strong>Lawn maintenance</strong>
      (cut &amp; trim) starting from
      <span class="price">$60</span>
    </div>
    <div class="price-item">
      <strong>Lawn rejuvenation</strong>
      starting from
      <span class="price">$80</span>
      <span class="note">(Only $27 a month for 3 months)*</span>
    </div>
    <div class="price-item">
      <strong>Package deal</strong>
      starting from
      <span class="price">$120</span>
    </div>
    <div class="intro-offer">
      <strong>Introductory offer:</strong>
      <span class="offer">25% off all services.</span>
      <small>Refer a friend, when they book you receive another 25% off your next service.</small>
    </div>
  </section>

  <div class="logo-badge"><span class="brand-name">Velvet Turf</span></div>

  <ul class="benefits">
    <li><svg viewBox="0 0 14 14"><circle cx="7" cy="7" r="6" fill="none" stroke="#8cc63f" stroke-width="1.8"/><path d="M4 7.2l2 2 4-4.4" fill="none" stroke="#8cc63f" stroke-width="1.8"/></svg>Instantly restores the natural green colour of grass – year round</li>
    <li><svg viewBox="0 0 14 14"><circle cx="7" cy="7" r="6" fill="none" stroke="#8cc63f" stroke-width="1.8"/><path d="M4 7.2l2 2 4-4.4" fill="none" stroke="#8cc63f" stroke-width="1.8"/></svg>Lasts for up to 3 months</li>
    <li><svg viewBox="0 0 14 14"><circle cx="7" cy="7" r="6" fill="none" stroke="#8cc63f" stroke-width="1.8"/><path d="M4 7.2l2 2 4-4.4" fill="none" stroke="#8cc63f" stroke-width="1.8"/></svg>Substantially reduces watering needs<br>Pet friendly</li>
    <li><svg viewBox="0 0 14 14"><circle cx="7" cy="7" r="6" fill="none" stroke="#8cc63f" stroke-width="1.8"/><path d="M4 7.2l2 2 4-4.4" fill="none" stroke="#8cc63f" stroke-width="1.8"/></svg>Stays green during droughts and water restrictions</li>
    <li><svg viewBox="0 0 14 14"><circle cx="7" cy="7" r="6" fill="none" stroke="#8cc63f" stroke-width="1.8"/><path d="M4 7.2l2 2 4-4.4" fill="none" stroke="#8cc63f" stroke-width="1.8"/></svg>UV fade resistant</li>
    <li><svg viewBox="0 0 14 14"><circle cx="7" cy="7" r="6" fill="none" stroke="#8cc63f" stroke-width="1.8"/><path d="M4 7.2l2 2 4-4.4" fill="none" stroke="#8cc63f" stroke-width="1.8"/></svg>Won’t bleed, run, or stain once absorbed into the grass</li>
    <li><svg viewBox="0 0 14 14"><circle cx="7" cy="7" r="6" fill="none" stroke="#8cc63f" stroke-width="1.8"/><path d="M4 7.2l2 2 4-4.4" fill="none" stroke="#8cc63f" stroke-width="1.8"/></svg>Safe for the environment, pets and people</li>
    <li><svg viewBox="0 0 14 14"><circle cx="7" cy="7" r="6" fill="none" stroke="#8cc63f" stroke-width="1.8"/><path d="M4 7.2l2 2 4-4.4" fill="none" stroke="#8cc63f" stroke-width="1.8"/></svg>Works in extreme heat, cold and frost</li>
    <li><svg viewBox="0 0 14 14"><circle cx="7" cy="7" r="6" fill="none" stroke="#8cc63f" stroke-width="1.8"/><path d="M4 7.2l2 2 4-4.4" fill="none" stroke="#8cc63f" stroke-width="1.8"/></svg>Organic and natural – no harmful chemicals</li>
    <li><svg viewBox="0 0 14 14"><circle cx="7" cy="7" r="6" fill="none" stroke="#8cc63f" stroke-width="1.8"/><path d="M4 7.2l2 2 4-4.4" fill="none" stroke="#8cc63f" stroke-width="1.8"/></svg>Reduces the amount of fertilizer and water used on lawns</li>
    <li><svg viewBox="0 0 14 14"><circle cx="7" cy="7" r="6" fill="none" stroke="#8cc63f" stroke-width="1.8"/><path d="M4 7.2l2 2 4-4.4" fill="none" stroke="#8cc63f" stroke-width="1.8"/></svg>Kerb appeal is essential for getting your property sold for the highest price possible</li>
  </ul>

  <div class="social">
    <span>Follow Us On:</span>
    <span class="network"><span class="dot"></span>Chatterbook</span>
    <span class="network"><span class="dot"></span>Snapgrid</span>
  </div>

  <div class="phone">
    <svg viewBox="0 0 24 24"><path d="M6.6 10.8a15 15 0 0 0 6.6 6.6l2.2-2.2a1 1 0 0 1 1-.25 11.4 11.4 0 0 0 3.6.57 1 1 0 0 1 1 1V20a1 1 0 0 1-1 1A17 17 0 0 1 3 4a1 1 0 0 1 1-1h3.5a1 1 0 0 1 1 1c0 1.25.2 2.45.57 3.6a1 1 0 0 1-.25 1z" fill="#6fa62a"/></svg>
    <span>: 555 0192 384</span>
  </div>
</main>
</body>
</html>
```